Oil and Gas Exploration and Production company needs a business card design

We need a business card design using our logo and colors in the logo. We want a mainstream design.

```html
<!DOCTYPE html>
<html lang="en">
<head>
<meta charset="utf-8">
<title>Vesta Oil &amp; Gas — Business Card</title>
<link rel="stylesheet" href="https://fonts.googleapis.com/css2?family=EB+Garamond:wght@400;600;700&display=swap">
<style>
  :root {
    --page-bg: #ececec;
    --card-bg: #f3f3f3;
    --decor: #e6e6e6;
    --gold: #c9962e;
    --ink: #1a1a1a;
  }
  html, body {
    margin: 0;
    width: 1200px;
    height: 586px;
    overflow: hidden;
    background: var(--page-bg);
  }
  .canvas {
    position: relative;
    width: 1200px;
    height: 586px;
    display: flex;
    align-items: center;
    justify-content: center;
  }
  .card {
    position: relative;
    width: 900px;
    height: 540px;
    background: var(--card-bg);
    overflow: hidden;
    font-family: "EB Garamond", Garamond, serif;
  }
  .card__decor {
    position: absolute;
    left: 330px;
    top: -130px;
    width: 860px;
    height: 860px;
    border-radius: 50%;
    background: var(--decor);
  }
  .brand {
    position: absolute;
    left: 58px;
    top: 226px;
    display: flex;
    align-items: center;
    gap: 14px;
  }
  .brand__dot {
    width: 44px;
    height: 44px;
    border-radius: 50%;
    background: var(--ink);
  }
  .brand__name {
    margin: 0;
    font-size: 54px;
    font-weight: 700;
    line-height: 1;
    color: var(--ink);
  }
  .contact {
    position: absolute;
    left: 538px;
    top: 196px;
    color: var(--ink);
  }
  .contact__name {
    margin: 0;
    font-size: 22px;
    font-weight: 700;
    color: var(--gold);
    line-height: 1.2;
  }
  .contact__role {
    margin: 2px 0 20px;
    font-size: 17px;
    line-height: 1.2;
  }
  .contact__list {
    list-style: none;
    margin: 0;
    padding: 0;
  }
  .contact__item {
    display: flex;
    align-items: center;
    gap: 16px;
    font-size: 19px;
    line-height: 1;
    margin-bottom: 17px;
  }
  .contact__icon {
    width: 18px;
    height: 18px;
    flex: none;
  }
  .contact__icon--social {
    width: 14px;
    height: 14px;
    margin: 0 2px;
    border-radius: 50%;
    background: var(--gold);
  }
  .contact__address {
    margin: 24px 0 0;
    font-size: 19px;
    font-weight: 600;
    color: var(--gold);
    line-height: 1.4;
  }
</style>
</head>
<body>
  <main class="canvas">
    <section class="card">
      <div class="card__decor" role="img" aria-label="Large faint company emblem in the background"></div>

      <div class="brand">
        <span class="brand__dot"></span>
        <h1 class="brand__name">Vesta Oil &amp; Gas</h1>
      </div>

      <div class="contact">
        <p class="contact__name">Marta Ellison</p>
        <p class="contact__role">Chief Executive Officer</p>
        <ul class="contact__list">
          <li class="contact__item">
            <svg class="contact__icon" viewBox="0 0 18 18" aria-hidden="true">
              <path fill="#c9962e" d="M2 6c0-2 2-3 7-3s7 1 7 3v1h-3V5.5c-1-.5-2.5-.7-4-.7s-3 .2-4 .7V7H2z"/>
              <path fill="#c9962e" d="M4 9l2-2h6l2 2v6H4z"/>
            </svg>
            <span>+34 900 412 358.</span>
          </li>
          <li class="contact__item">
            <svg class="contact__icon" viewBox="0 0 18 18" aria-hidden="true">
              <rect x="1" y="4" width="16" height="11" fill="#c9962e"/>
              <path d="M1.5 4.5L9 10l7.5-5.5" fill="none" stroke="#f3f3f3" stroke-width="1.4"/>
            </svg>
            <span>info@vestaoilgas</span>
          </li>
          <li class="contact__item">
            <span class="contact__icon contact__icon--social"></span>
            <span>@vestaoilgas</span>
          </li>
        </ul>
        <p class="contact__address">Calle del Prado 14<br>Oficina 2B, 24010, Ribera</p>
      </div>
    </section>
  </main>
</body>
</html>
```